Mental Health care Company in Washington DC

We are a new mental health care services provider in Washington DC. Please look at these sites.
https://brightwaterfamilysupport.com
https://www.quietharborinc.com
https://willowgate-dc.org/
https://www.tidepathdc.com
https://www.thelanternofdc.com

```html
<!DOCTYPE html>
<html lang="en">
<head>
<meta charset="utf-8">
<title>Calder Health Services — Mental Health Care in Washington DC</title>
<link rel="stylesheet" href="https://fonts.googleapis.com/css2?family=Poppins:ital,wght@0,300;0,400;0,500;0,600;0,700;0,800;1,400&display=swap">
<style>
:root{
  --navy:#14234b;
  --navy-deep:#12204a;
  --teal:#a9dbe0;
  --teal-soft:#cdeaed;
  --orange:#f3a25e;
  --grey-bg:#efefef;
  --text:#3d4150;
  --muted:#8e939c;
  --white:#ffffff;
}
*{margin:0;padding:0;box-sizing:border-box}
html,body{width:1200px;height:4464px;overflow:hidden}
body{font-family:"Poppins",sans-serif;color:var(--text);background:var(--white);position:relative}
.abs{position:absolute}
.btn{position:absolute;display:flex;align-items:center;justify-content:center;font-size:12px;font-weight:500;letter-spacing:.3px;color:var(--navy);background:var(--teal);text-transform:uppercase}
.btn-orange{background:var(--orange)}
.section-title{position:absolute;left:0;width:1200px;text-align:center;font-size:31px;font-weight:400;color:var(--navy);letter-spacing:.3px}
.section-title b{font-weight:800}

/* header */
.site-header{position:absolute;top:0;left:0;width:1200px;height:94px;background:var(--white)}
.brand{position:absolute;left:142px;top:26px;display:flex;align-items:center;gap:10px}
.brand-dot{width:12px;height:12px;border-radius:50%;background:var(--teal)}
.brand-name{font-size:30px;font-weight:500;color:var(--navy);line-height:1}
.brand-sub{position:absolute;left:142px;top:62px;width:170px;text-align:center;font-size:10px;letter-spacing:6px;color:var(--muted)}
.main-nav{position:absolute;top:38px;left:527px;display:flex;gap:45px;font-size:12px;font-weight:500;color:var(--navy)}
.nav-contact{left:932px;top:26px;width:127px;height:42px}

/* hero */
.hero-photo{position:absolute;top:94px;left:0;width:1200px;height:660px;background:linear-gradient(100deg,#e7d9cc 0%,#d6c2b1 45%,#a7836b 75%,#6b4d3e 100%)}
.hero-copy{position:absolute;left:142px;top:256px;color:var(--navy)}
.hero-copy .l1{font-size:33px;font-weight:400;line-height:1.2}
.hero-copy .l2{font-size:41px;font-weight:700;line-height:1.25}
.hero-copy .l3{font-size:31px;font-weight:400;line-height:1.25}
.hero-copy p{margin-top:18px;font-size:17.5px;line-height:1.45;color:#1f2a44}
.hero-cta{left:142px;top:486px;width:204px;height:40px}

/* about */
.about-photo{position:absolute;left:140px;top:790px;width:460px;height:560px;background:radial-gradient(ellipse at 50% 50%,#cfdfe3 0%,#dde6ea 45%,#f2f5f6 75%,#fff 100%)}
.about-title{position:absolute;left:668px;top:858px;font-size:31px;color:var(--navy);font-weight:400}
.about-title b{font-weight:800}
.about-sub{position:absolute;left:666px;top:899px;font-size:20px;color:#b5b9bf;display:flex;align-items:center;gap:10px}
.about-sub span{display:block;width:82px;height:1px;background:#b5b9bf}
.about-text{position:absolute;left:668px;top:940px;width:390px;font-size:13px;line-height:21.5px;color:var(--text)}
.about-text p+p{margin-top:14px}
.about-btn{left:668px;top:1217px;width:126px;height:40px}

/* services */
.services{position:absolute;top:1387px;left:0;width:1200px;height:550px;background:var(--grey-bg)}
.service-card{position:absolute;top:151px;width:284px;height:304px;background:var(--white);border-radius:6px;box-shadow:0 6px 18px rgba(0,0,0,.06);text-align:center}
.service-icon{width:84px;height:84px;margin:34px auto 0;border-radius:50%;border:2px dashed var(--teal);display:flex;align-items:center;justify-content:center}
.service-icon.orange{border-color:var(--orange)}
.service-icon i{display:block;width:68px;height:68px;border-radius:50%;background:var(--teal)}
.service-icon.orange i{background:var(--orange)}
.service-card h3{margin-top:20px;font-size:18px;font-weight:500;color:var(--navy)}
.service-card p{margin:12px auto 0;width:250px;font-size:13px;line-height:21.5px;color:var(--text)}

/* testimonials */
.avatar{position:absolute;border-radius:50%;background:linear-gradient(160deg,#d9dbde,#8d939b)}
.stars{position:absolute;top:2098px;left:0;width:1200px;text-align:center;color:var(--orange);font-size:20px;letter-spacing:4px}
.quote{position:absolute;top:2136px;left:320px;width:560px;text-align:center;font-style:italic;font-size:15px;line-height:24px;color:#3f4452}
.quote-name{position:absolute;top:2274px;left:0;width:1200px;text-align:center;font-size:16px;font-weight:600;color:var(--navy);letter-spacing:.5px}
.quote-place{position:absolute;top:2300px;left:0;width:1200px;text-align:center;font-size:14px;color:var(--text)}
.dots{position:absolute;top:2334px;left:575px;display:flex;gap:12px}
.dots span{width:9px;height:9px;border-radius:50%;border:1px solid #8e939c}
.dots span.on{background:var(--teal);border-color:var(--teal)}

/* why */
.why{position:absolute;top:2459px;left:0;width:1200px;height:711px;background:var(--grey-bg)}
.why-item h4{font-size:18px;font-weight:600;color:var(--navy)}
.why-item p{margin-top:6px;font-size:13px;line-height:21.5px;color:var(--text)}
.why-icon{position:absolute;width:100px;height:100px;border-radius:50%;background:var(--white);box-shadow:0 4px 14px rgba(0,0,0,.1);display:flex;align-items:center;justify-content:center}

/* contact */
.field{position:absolute;height:41px;border:1px solid #d8dadd;border-radius:3px;background:var(--white);display:flex;align-items:center;font-size:11px;color:#555}
.field .ico{width:34px;height:100%;border-right:1px solid #d8dadd;display:flex;align-items:center;justify-content:center;margin-right:12px}
.field .ico i{width:9px;height:9px;border-radius:50%;background:var(--orange)}
.field.tall{height:85px;align-items:flex-start}
.field.tall .ico{height:100%;align-items:flex-start;padding-top:14px}
.field.tall span{padding-top:13px}

/* cta */
.cta-photo{position:absolute;top:3728px;left:0;width:1200px;height:356px;background:linear-gradient(180deg,#8fa5b6 0%,#6b8292 30%,#3a4d3e 55%,#1f3a55 75%,#2f5a7a 100%)}
.cta-title{position:absolute;top:3804px;left:0;width:1200px;text-align:center;font-size:27px;color:var(--white);font-weight:400}
.cta-title b{font-weight:700}
.cta-sub{position:absolute;top:3846px;left:0;width:1200px;text-align:center;font-size:21px;color:var(--white);font-weight:300}
.cta-btn{left:497px;top:3890px;width:205px;height:41px}

/* footer */
.site-footer{position:absolute;top:4084px;left:0;width:1200px;height:380px;background:var(--navy-deep);color:var(--white)}
.foot-col{position:absolute;top:64px}
.foot-col h5{font-size:15px;font-weight:700;letter-spacing:.3px;margin-bottom:22px}
.quick li{list-style:none;font-size:12.5px;line-height:28px}
.contact-row{display:flex;gap:12px;margin-bottom:18px;font-size:12px;line-height:18px}
.contact-row b{font-weight:600;display:block}
.pin{width:10px;height:10px;border-radius:50%;background:var(--white);margin-top:4px;flex:none}
.social li{list-style:none;display:flex;align-items:center;gap:12px;font-size:12.5px;margin-bottom:12px}
.social i{width:29px;height:29px;border:1px solid rgba(255,255,255,.8);border-radius:50%;display:flex;align-items:center;justify-content:center}
.social i::after{content:"";width:8px;height:8px;border-radius:50%;background:var(--white)}
.foot-line{position:absolute;top:320px;left:142px;width:918px;height:1px;background:rgba(255,255,255,.2)}
.copyright{position:absolute;top:344px;left:0;width:1200px;text-align:center;font-size:12px;color:rgba(255,255,255,.85)}
</style>
</head>
<body>

<header class="site-header">
  <div class="brand"><span class="brand-dot"></span><span class="brand-name">Calder Health</span></div>
  <div class="brand-sub">SERVICES</div>
  <nav class="main-nav"><span>HOME</span><span>ABOUT US</span><span>SERVICES</span><span>OUR TEAM</span></nav>
  <div class="btn nav-contact">Contact Us</div>
</header>

<section class="hero">
  <div class="hero-photo" role="img" aria-label="Hands holding a paper head silhouette with a colourful puzzle heart"></div>
  <svg class="abs" style="top:560px;left:0" width="1200" height="220" viewBox="0 0 1200 220">
    <path d="M0 50 C150 160 360 165 560 125 C760 85 900 70 1200 55 L1200 220 L0 220 Z" fill="#fff"/>
  </svg>
  <div class="hero-copy">
    <div class="l1">Compassionate</div>
    <div class="l2">Mental Health Care</div>
    <div class="l3">in Washington DC</div>
    <p>Your journey to wellness begins with understanding.<br>We’re here to guide you every step of the way.</p>
  </div>
  <div class="btn hero-cta">Schedule Consultation</div>
</section>

<section class="about">
  <div class="about-photo" role="img" aria-label="Woman holding a standing yoga pose in soft light"></div>
  <h2 class="about-title">ABOUT <b>CALDER HEALTH</b></h2>
  <div class="about-sub">SERVICES <span></span></div>
  <div class="about-text">
    <p>Lorem ipsum dolor sit amet, consectetuer adipiscing elit sed diam nonummy nibh euismod tincidunt ut laoet dolo magna aliquam erat volutpat.</p>
    <p>Ut wisi enim ad minim veniam, quis nostrud exer ullamcorper suscipit lobortis nisl ut aliquip ex ea commodo consequat. Duis autem vel eum iriure dolor in hendrerit in vulputate velit esse molestie consequat, vel illum dolore eu feugilla facilisis at vero eros et accumsan et iusto odio dignissim qui blandit praesent luptatum zzril delenit augue duis dolore te feugait nulla facilisi. Lorem ipsum dolor sit amet, consectetuer adipiscing elit, sed diam nonummy.</p>
  </div>
  <div class="btn about-btn">Read More</div>
</section>

<section class="services">
  <h2 class="section-title" style="top:84px">OUR <b>SERVICES</b></h2>
  <article class="service-card" style="left:142px">
    <div class="service-icon"><i></i></div>
    <h3>Individual Therapy</h3>
    <p>Ut wisi enim ad minim v quis nostrud exerci taton ullamcorper spit lobortis nisl ut aliquip ex ea comghmodo consequat. Duis autem vel eum iriure dolor in hendrerit in vulputa.</p>
  </article>
  <article class="service-card" style="left:457px">
    <div class="service-icon orange"><i></i></div>
    <h3>Group Therapy</h3>
    <p>Ut wisi enim ad minim v quis nostrud exerci taton ullamcorper spit lobortis nisl ut aliquip ex ea comghmodo consequat. Duis autem vel eum iriure dolor in hendrerit in vulputa.</p>
  </article>
  <article class="service-card" style="left:775px">
    <div class="service-icon"><i></i></div>
    <h3>Psychiatric Services</h3>
    <p>Ut wisi enim ad minim v quis nostrud exerci taton ullamcorper spit lobortis nisl ut aliquip ex ea comghmodo consequat. Duis autem vel eum iriure dolor in hendrerit in vulputa.</p>
  </article>
</section>

<section class="testimonials">
  <h2 class="section-title" style="top:2020px">WHAT OUR <b>CLIENTS SAY</b></h2>
  <div class="avatar" style="left:229px;top:2016px;width:96px;height:96px" role="img" aria-label="Client portrait"></div>
  <div class="avatar" style="left:123px;top:2166px;width:66px;height:66px" role="img" aria-label="Client portrait"></div>
  <div class="avatar" style="left:250px;top:2285px;width:80px;height:80px" role="img" aria-label="Client portrait"></div>
  <div class="avatar" style="left:983px;top:2041px;width:114px;height:114px" role="img" aria-label="Client portrait"></div>
  <div class="avatar" style="left:895px;top:2225px;width:100px;height:100px" role="img" aria-label="Client portrait"></div>
  <div class="stars">★★★★★</div>
  <p class="quote">"Lorem ipsum dolor sit amet, consectetuer adipiscing elit, sed diam nonummy nibh euismod tincidunt ut laoreet dolore magna aliquam erat volutpat. Ut wisi enim ad minim veniam, quis nostrud exerci tation ullamcorper suscipit lobortis nisl ut aliquip ex ea commodo consequat. Duis autem vel eum iriure dolor in hendrerit in vulputate velit."</p>
  <div class="quote-name">DANA &amp; OWEN T.</div>
  <div class="quote-place">Austin, TX</div>
  <div class="dots"><span></span><span class="on"></span><span></span></div>
</section>

<section class="why">
  <h2 class="section-title" style="top:86px">WHY <b>CHOOSE US</b></h2>
  <svg class="abs" style="left:398px;top:141px" width="400" height="400" viewBox="0 0 400 400">
    <circle cx="200" cy="200" r="190" fill="#fff"/>
    <path d="M90 45 A190 190 0 0 0 118 372" fill="none" stroke="#a9dbe0" stroke-width="2"/>
    <path d="M290 32 A190 190 0 0 1 308 356" fill="none" stroke="#f3a25e" stroke-width="2"/>
    <circle cx="90" cy="45" r="5" fill="#fff" stroke="#a9dbe0" stroke-width="2"/>
    <circle cx="392" cy="200" r="5" fill="#fff" stroke="#f3a25e" stroke-width="2"/>
    <circle cx="118" cy="372" r="5" fill="#fff" stroke="#a9dbe0" stroke-width="2"/>
    <circle cx="200" cy="200" r="70" fill="#eef7f8"/>
  </svg>
  <svg class="abs" style="left:374px;top:196px" width="120" height="120" viewBox="0 0 120 120"><path d="M60 0 A60 60 0 0 1 120 60 L95 60 A35 35 0 0 0 60 25 Z" fill="#a9dbe0"/><path d="M0 60 A60 60 0 0 0 60 120 L60 95 A35 35 0 0 1 25 60 Z" fill="#a9dbe0"/></svg>
  <div class="why-icon" style="left:384px;top:196px"><svg width="40" height="40" viewBox="0 0 40 40"><rect x="6" y="6" width="22" height="28" rx="2" fill="none" stroke="#14234b" stroke-width="2"/><circle cx="28" cy="28" r="8" fill="#fff" stroke="#14234b" stroke-width="2"/><path d="M28 24v4h3" stroke="#14234b" stroke-width="2" fill="none"/></svg></div>
  <svg class="abs" style="left:703px;top:196px" width="120" height="120" viewBox="0 0 120 120"><path d="M0 60 A60 60 0 0 1 60 0 L60 25 A35 35 0 0 0 25 60 Z" fill="#a9dbe0"/><path d="M60 120 A60 60 0 0 0 120 60 L95 60 A35 35 0 0 1 60 95 Z" fill="#a9dbe0"/></svg>
  <div class="why-icon" style="left:713px;top:196px"><svg width="40" height="40" viewBox="0 0 40 40"><circle cx="20" cy="13" r="7" fill="none" stroke="#14234b" stroke-width="2"/><path d="M7 36c0-8 6-13 13-13s13 5 13 13" fill="none" stroke="#14234b" stroke-width="2"/></svg></div>
  <svg class="abs" style="left:538px;top:468px" width="120" height="70" viewBox="0 0 120 70"><path d="M0 60 A60 60 0 0 1 120 60 L95 60 A35 35 0 0 0 25 60 Z" fill="#f3a25e"/></svg>
  <div class="why-icon" style="left:548px;top:468px"><svg width="44" height="44" viewBox="0 0 44 44"><circle cx="22" cy="22" r="18" fill="none" stroke="#14234b" stroke-width="2"/><circle cx="22" cy="22" r="11" fill="none" stroke="#14234b" stroke-width="2"/><circle cx="22" cy="19" r="4" fill="none" stroke="#14234b" stroke-width="2"/></svg></div>
  <div class="why-item abs" style="left:112px;top:196px;width:250px;text-align:right">
    <h4>Flexible Scheduling</h4>
    <p>We offer evening and weekend appointments to accommodate your busy lifestyle.</p>
  </div>
  <div class="why-item abs" style="left:832px;top:196px;width:260px">
    <h4>Experienced Therapists</h4>
    <p>Our team consists of licensed professionals with years of experience in various mental health specialties.</p>
  </div>
  <div class="why-item abs" style="left:668px;top:533px;width:250px">
    <h4>Personalized Approach</h4>
    <p>We develop individualized treatment plans tailored to your unique needs and circumstances.</p>
  </div>
</section>

<section class="contact">
  <h2 class="section-title" style="top:3256px">GET IN <b>TOUCH</b></h2>
  <p class="abs" style="top:3306px;left:370px;width:460px;text-align:center;font-size:13px;line-height:22px">Lorem ipsum dolor sit amet, consectetuer adipiscing elit sed diam nonummy nibh euismod tincidunt.</p>
  <div class="field" style="left:302px;top:3370px;width:290px"><span class="ico"><i></i></span><span>First Name*</span></div>
  <div class="field" style="left:607px;top:3370px;width:290px"><span class="ico"><i></i></span><span>Last Name*</span></div>
  <div class="field" style="left:302px;top:3425px;width:290px"><span class="ico"><i></i></span><span>Your Phone*</span></div>
  <div class="field" style="left:607px;top:3425px;width:290px"><span class="ico"><i></i></span><span>Your Email*</span></div>
  <div class="field tall" style="left:302px;top:3480px;width:595px"><span class="ico"><i></i></span><span>Your Message</span></div>
  <div class="btn" style="left:536px;top:3622px;width:127px;height:40px">Submit Now</div>
</section>

<section class="cta">
  <div class="cta-photo" role="img" aria-label="Person meditating on a dock by a mountain lake"></div>
  <h2 class="cta-title">READY TO START YOUR <b>JOURNEY TO WELLNESS?</b></h2>
  <p class="cta-sub">Schedule a consultation with one of our experienced therapists today.</p>
  <div class="btn btn-orange cta-btn">Schedule Consultation</div>
</section>

<footer class="site-footer">
  <div class="foot-col" style="left:142px">
    <h5>QUICK LINKS</h5>
    <ul class="quick"><li>• Home</li><li>• About Us</li><li>• Services</li><li>• Our Team</li><li>• Contact Us</li></ul>
  </div>
  <div class="foot-col" style="left:370px">
    <h5>CONTACT DETAILS</h5>
    <div class="contact-row"><span class="pin"></span><div><b>ADDRESS</b>48 Larkspur Row, Suite 210<br>Washington, DC.</div></div>
    <div class="contact-row"><span class="pin"></span><div><b>PHONE</b>202 555 0148</div></div>
    <div class="contact-row"><span class="pin"></span><div><b>EMAIL</b>info@calderhealth.com</div></div>
  </div>
  <div class="foot-col" style="left:673px">
    <h5>FOLLOW US</h5>
    <ul class="social"><li><i></i>Community</li><li><i></i>Videos</li><li><i></i>Photos</li><li><i></i>Updates</li></ul>
  </div>
  <div class="foot-line"></div>
  <div class="copyright">© 2025 Calder Health Services. All Rights Reserved.</div>
</footer>

</body>
</html>
```